Harborline Renewal Business Card Design

Professional and clean design. The design colors should flow with the logo. Two-sided card with the website on the back which is:

www.HarborlineRenewal.example.

"Specializing in Water Damage Restoration"

On the front I need the name, email, phone, and logo.

Name: Darnell Quisby
Email: Darnell@HarborlineRenewal.example
Phone: 555-318-2046 for now

I only have the Preview and Thumbnail right now but should have the source files uploaded within a day or two.

Target Market(s)

Flood victims, home owners with water damage from busted pipes etc...

Industry/Entity Type

Business

Contact Information for Business Card

Name: Darnell Quisby

Font styles to use
Serif
Sans Serif

Requirements
Must have
• Business Card Details Info

```html
<!DOCTYPE html>
<html lang="en">
<head>
<meta charset="utf-8">
<title>Harborline Renewal Business Card</title>
<link rel="stylesheet" href="https://fonts.googleapis.com/css2?family=Open+Sans:wght@400;700&display=swap">
<style>
  :root {
    --stage: #2b2b2b;
    --card-black: #050505;
    --brand-blue: #2596d6;
    --brand-blue-light: #4fbbee;
    --text-blue: #2a8fcf;
    --white: #ffffff;
  }
  html, body {
    margin: 0;
    padding: 0;
    width: 1200px;
    height: 900px;
    overflow: hidden;
    background: var(--stage);
    font-family: "Open Sans", Arial, sans-serif;
  }
  .canvas {
    position: relative;
    width: 1200px;
    height: 900px;
  }
  .card {
    position: absolute;
    width: 600px;
    height: 343px;
    border-radius: 22px;
    background: var(--card-black);
    overflow: hidden;
    box-shadow: 0 12px 30px rgba(0,0,0,0.45);
  }
  .card-back { left: 80px; top: 70px; }
  .card-front { left: 520px; top: 487px; }

  /* back side */
  .back-brand {
    position: absolute;
    left: 0; right: 0; top: 70px;
    display: flex;
    flex-direction: column;
    align-items: center;
    gap: 16px;
  }
  .brand-dot {
    width: 110px;
    height: 110px;
    border-radius: 50%;
    background: var(--brand-blue);
  }
  .brand-name {
    color: var(--brand-blue);
    font-weight: 700;
    font-size: 26px;
    letter-spacing: 1px;
  }
  .tagline {
    position: absolute;
    left: 0; right: 0; top: 262px;
    text-align: center;
    color: var(--text-blue);
    font-size: 15px;
    letter-spacing: 0.6px;
    line-height: 1.35;
  }
  .tagline .headline { text-transform: uppercase; }

  /* front side */
  .front-shape {
    position: absolute;
    inset: 0;
  }
  .contact {
    position: absolute;
    left: 38px;
    top: 148px;
    color: var(--white);
  }
  .contact-name {
    margin: 0 0 12px;
    font-size: 25px;
    font-weight: 700;
    text-transform: uppercase;
    letter-spacing: 0.5px;
  }
  .contact-list {
    list-style: none;
    margin: 0;
    padding: 0;
    font-size: 15px;
    line-height: 1.45;
  }
  .contact-list li {
    display: flex;
    align-items: center;
    gap: 10px;
  }
  .contact-list svg { width: 13px; height: 13px; flex: none; }
  .front-brand {
    position: absolute;
    right: 28px;
    top: 70px;
    width: 210px;
    display: flex;
    flex-direction: column;
    align-items: center;
    gap: 10px;
  }
  .front-brand .brand-dot { width: 58px; height: 58px; }
  .front-brand .brand-name { font-size: 22px; letter-spacing: 0.5px; }
</style>
</head>
<body>
<main class="canvas">

  <section class="card card-back" aria-label="Card back">
    <div class="back-brand">
      <div class="brand-dot"></div>
      <div class="brand-name">Harborline Renewal</div>
    </div>
    <p class="tagline">
      <span class="headline">Specializing in Water Damage Restoration</span><br>
      www.HarborlineRenewal.example
    </p>
  </section>

  <section class="card card-front" aria-label="Card front">
    <svg class="front-shape" viewBox="0 0 600 343" preserveAspectRatio="none">
      <path d="M0 0 H245 C330 30 370 180 335 300 C325 325 318 335 310 343 H0 Z" fill="var(--brand-blue)"/>
      <path d="M245 0 C335 28 378 180 343 300 C335 322 328 334 318 343" fill="none" stroke="var(--brand-blue)" stroke-width="3"/>
      <path d="M236 0 C322 34 362 180 327 300 C320 320 313 332 303 343" fill="none" stroke="var(--card-black)" stroke-width="2"/>
    </svg>

    <div class="contact">
      <h2 class="contact-name">Darnell Quisby</h2>
      <ul class="contact-list">
        <li>
          <svg viewBox="0 0 24 24"><path d="M6.6 10.8a15 15 0 0 0 6.6 6.6l2.2-2.2c.3-.3.7-.4 1-.2 1.1.4 2.3.6 3.6.6.6 0 1 .4 1 1V20c0 .6-.4 1-1 1A17 17 0 0 1 3 4c0-.6.4-1 1-1h3.5c.6 0 1 .4 1 1 0 1.3.2 2.5.6 3.6.1.3 0 .7-.2 1z" fill="var(--white)"/></svg>
          555-318-2046
        </li>
        <li>
          <svg viewBox="0 0 24 24"><rect x="3" y="5" width="18" height="14" rx="1.5" fill="none" stroke="var(--white)" stroke-width="2"/><path d="M3 6l9 7 9-7" fill="none" stroke="var(--white)" stroke-width="2"/></svg>
          Darnell@HarborlineRenewal.example
        </li>
        <li>
          <svg viewBox="0 0 24 24"><circle cx="12" cy="12" r="9" fill="none" stroke="var(--white)" stroke-width="2"/><path d="M3 12h18M12 3c3 3 3 15 0 18M12 3c-3 3-3 15 0 18" fill="none" stroke="var(--white)" stroke-width="1.6"/></svg>
          www.HarborlineRenewal.example
        </li>
      </ul>
    </div>

    <div class="front-brand">
      <div class="brand-dot"></div>
      <div class="brand-name">Harborline Renewal</div>
    </div>
  </section>

</main>
</body>
</html>
```